Ridgeline Haul Carriers - Website

A clean, not cluttered informative website for our business. We specialize in the transportation of radioactive materials across North America. The site is mostly for information about our company and will not be used to attract business but will be used to attract employee's mainly drivers. Driver's are very hard to find in our area. One of the pages needs to be a job's posting page with an apply now button. Either an application can be filled out there or a resume can be uploaded which ever functionality works better. I would like a website that I can easily edit, ability to change text and photos.

Number of Pages Required

5+ page

Colors

Designer to choose colors to be used in the design.

Requirements
Must have
• Home - About - Services - Jobs - Contact pages
• A way prospective employee's can apply or upload their resume to be emailed to me
• Very clean apperance
Should not have
• I don't want it to be busy

```html
<!DOCTYPE html>
<html lang="en">
<head>
<meta charset="utf-8">
<title>Ridgeline Haul Carriers</title>
<link href="https://fonts.googleapis.com/css2?family=Poppins:wght@400;500;600;700&display=swap" rel="stylesheet">
<style>
:root{
  --red:#e31b23;
  --red-deep:#b3121a;
  --ink:#222;
  --muted:#555;
  --white:#fff;
  --black:#111;
  --line:#d8d8d8;
}
*{box-sizing:border-box;margin:0;padding:0}
html,body{width:1200px;height:3482px;overflow:hidden}
body{font-family:"Poppins",sans-serif;color:var(--ink);background:var(--white);position:relative}
.abs{position:absolute}
a{color:inherit;text-decoration:none}

/* hero */
.hero{position:absolute;left:0;top:0;width:1200px;height:715px;
  background:linear-gradient(180deg,#5b6670 0%,#7d858c 35%,#4a4f55 70%,#3a3d40 100%);}
.hero-shade{position:absolute;inset:0;background:linear-gradient(180deg,rgba(20,30,40,.55),rgba(0,0,0,.15) 40%,rgba(0,0,0,.25))}
.topbar{position:absolute;top:0;left:0;width:1200px;height:50px;color:var(--white);font-size:14px}
.topbar span{position:absolute;top:15px;display:flex;align-items:center;gap:8px}
.topbar svg{fill:var(--red)}
.brand{position:absolute;left:97px;top:78px;color:var(--white);font-weight:700;font-size:34px;letter-spacing:1px;line-height:1.1}
.nav{position:absolute;top:86px;font-size:17px;color:var(--white);font-weight:500}
.nav a{position:absolute;white-space:nowrap}
.nav .active{color:var(--red)}
.hero h1{position:absolute;top:304px;width:1200px;text-align:center;color:var(--white);font-size:41px;font-weight:600}
.hero p{position:absolute;top:362px;left:300px;width:600px;text-align:center;color:var(--white);font-size:23px;line-height:40px;font-weight:500}
.btn{display:inline-flex;align-items:center;justify-content:center;border-radius:30px;font-weight:600}
.hero .btn{position:absolute;left:490px;top:452px;width:220px;height:56px;background:var(--red);color:var(--white);font-size:17px}
.social{position:absolute;left:44px;top:292px}
.social i{display:block;width:14px;height:14px;border-radius:50%;background:var(--white);margin-bottom:26px}
.follow{position:absolute;left:40px;top:490px;color:var(--white);font-size:13px;transform:rotate(-90deg);transform-origin:left top}
.dots{position:absolute;left:1146px;top:352px}
.dots i{display:block;width:12px;height:12px;border-radius:50%;background:var(--white);margin-bottom:24px}
.dots i.on{width:20px;height:20px;margin-left:-4px;border:4px solid var(--white);background:transparent;box-shadow:inset 0 0 0 3px #555;background:var(--white)}

/* contact form */
.touch h2{position:absolute;top:784px;width:1200px;text-align:center;color:var(--red);font-size:27px;font-weight:700}
.touch p{position:absolute;top:838px;width:1200px;text-align:center;font-size:16px;color:var(--ink)}
.field{position:absolute;width:230px;height:40px;border:1px solid var(--line);font-size:12px;color:#666;padding:11px 14px;box-shadow:0 1px 4px rgba(0,0,0,.08)}
.submit{position:absolute;left:614px;top:948px;width:226px;height:38px;background:var(--red);color:var(--white);font-size:14px;font-weight:600;display:flex;align-items:center;justify-content:center}

/* about */
.about{position:absolute;left:0;top:1075px;width:1200px;height:503px;background:linear-gradient(100deg,#c4141d 0%,#e42a31 45%,#d01820 70%,#a30f16 100%)}
.about h2{position:absolute;left:88px;top:113px;color:var(--white);font-size:30px;font-weight:600}
.about p{position:absolute;left:88px;top:162px;width:510px;color:var(--white);font-size:14px;line-height:29px}
.about .btn{position:absolute;left:88px;top:360px;width:144px;height:46px;background:var(--white);color:var(--red);font-size:16px}
.photo{position:absolute;border-radius:50%;border:5px solid var(--white)}

/* services */
.services h2{position:absolute;left:566px;top:1720px;color:var(--red);font-size:33px;font-weight:600}
.services p{position:absolute;left:566px;top:1776px;width:556px;font-size:16px;line-height:29px;color:var(--muted);text-align:justify}
.services .btn{position:absolute;left:566px;top:1978px;width:180px;height:52px;background:var(--red-deep);color:var(--white);font-size:17px}

/* employment */
.jobs{position:absolute;left:0;top:2182px;width:1200px;height:596px;background:linear-gradient(120deg,#4a4038 0%,#6c2a2a 40%,#7e1e22 60%,#3c3a3a 100%)}
.jobs h2{position:absolute;top:90px;width:1200px;text-align:center;color:var(--white);font-size:33px;font-weight:600}
.job{position:absolute;top:158px;width:330px}
.job .pic{height:197px}
.job .apply{position:absolute;left:16px;top:180px;width:140px;height:32px;background:var(--red);color:var(--white);font-size:14px;font-weight:600;display:flex;align-items:center;justify-content:center}
.job h3{margin-top:34px;color:var(--white);font-size:17px;font-weight:600}
.job p{margin-top:8px;color:var(--white);font-size:11.5px;line-height:25px}

/* map */
.map{position:absolute;left:0;top:2778px;width:1200px;height:351px;background:linear-gradient(110deg,#dfe8d8 0%,#e9ece5 40%,#d6e6cf 70%,#c9e0c0 100%)}
.mapcard{position:absolute;left:448px;top:72px;width:295px;height:174px;background:var(--white);padding:22px 32px;font-size:14px;line-height:27px;color:var(--ink);box-shadow:0 2px 8px rgba(0,0,0,.15)}

/* footer */
.footer{position:absolute;left:0;top:3129px;width:1200px;height:299px;background:var(--black);color:var(--white)}
.footer .brand{left:97px;top:128px;font-size:30px;color:var(--red)}
.footer h4{position:absolute;top:46px;font-size:18px;font-weight:600}
.finfo{position:absolute;left:402px;font-size:14px;line-height:27px;display:flex;gap:16px}
.finfo svg{fill:var(--white);flex:none;margin-top:5px}
.flinks{position:absolute;left:685px;top:90px;font-size:14px;line-height:29px}
.fnews{position:absolute;left:840px;top:84px;width:260px;font-size:14px;line-height:27px}
.finput{position:absolute;left:840px;top:207px;width:213px;height:42px;background:var(--white);color:#555;font-size:11px;padding:14px 12px}
.fgo{position:absolute;left:1053px;top:207px;width:43px;height:42px;background:var(--red);display:flex;align-items:center;justify-content:center}
.copy{position:absolute;left:0;top:3428px;width:1200px;height:54px;background:var(--red);color:var(--white);font-size:14px;text-align:center;line-height:54px}
</style>
</head>
<body>

<header class="hero">
  <div class="abs" style="inset:0" role="img" aria-label="Photo of a row of parked semi trucks under a cloudy sky"></div>
  <div class="hero-shade"></div>
  <div class="topbar">
    <span style="left:88px"><svg width="12" height="14" viewBox="0 0 12 16"><path d="M6 0a6 6 0 0 0-6 6c0 4.5 6 10 6 10s6-5.5 6-10a6 6 0 0 0-6-6zm0 8.5A2.5 2.5 0 1 1 6 3.5a2.5 2.5 0 0 1 0 5z"/></svg>48 Harlow Creek Road, Kelmscott, WA 6111</span>
    <span style="left:432px"><svg width="14" height="11" viewBox="0 0 16 12"><path d="M0 0h16v12H0z"/></svg>info@ridgelinehaul.com</span>
    <span style="left:829px"><svg width="13" height="13" viewBox="0 0 16 16"><path d="M3.6 0 6 3.6 4.3 5.6a10 10 0 0 0 6.1 6.1l2-1.7L16 12.4 13.7 16C6 15.4.6 10 0 2.3z"/></svg>555 014 2290</span>
    <span style="left:1018px"><svg width="14" height="10" viewBox="0 0 14 10"><rect width="14" height="10"/></svg>English &#9662;</span>
  </div>
  <div class="brand">RIDGELINE HAUL<br>CARRIERS</div>
  <nav class="nav">
    <a class="active" style="left:644px">Home</a>
    <a style="left:738px">About</a>
    <a style="left:835px">Services</a>
    <a style="left:951px">Jobs</a>
    <a style="left:1035px">Contact</a>
  </nav>
  <div class="social"><i></i><i></i></div>
  <div class="follow">Follow us</div>
  <h1>WELCOME TO RIDGELINE HAUL CARRIERS</h1>
  <p>Sed ut perspiciatis unde omnis iste natus error sit voluptatem accusantium doloremque laudantium</p>
  <a class="btn">READ MORE</a>
  <div class="dots"><i></i><i class="on"></i><i></i></div>
</header>

<section class="touch">
  <h2>GET IN TOUCH</h2>
  <p>Sed ut perspiciatis unde omnis iste natus error sit voluptatem accusantium doloremque laudantium</p>
  <div class="field" style="left:107px;top:890px">Name</div>
  <div class="field" style="left:357px;top:890px">Email</div>
  <div class="field" style="left:614px;top:890px">Phone Number</div>
  <div class="field" style="left:865px;top:890px">Your Comapny</div>
  <div class="field" style="left:357px;top:948px;height:38px">Load Trooking<span style="position:absolute;right:14px;color:var(--red)">&#9660;</span></div>
  <div class="submit">SUBMIT</div>
</section>

<section class="about">
  <div class="abs" style="inset:0;background:radial-gradient(ellipse at 55% 60%,rgba(120,0,0,.35),transparent 60%)" role="img" aria-label="Red-toned photo of a truck on an open road"></div>
  <h2>ABOUT US</h2>
  <p>Sed ut perspiciatis unde omnis iste natus error sit voluptatem accusantium doloremque laudantium, totam rem aperiam, eaque ipsa quae ab illo inventore veritatis et quasi architecto beatae vitae dicta sunt explicabo. Nemo enim ipsam voluptatem quia voluptas sit aspernatur aut odit aut fugit, sed quia consequuntur magni dolores eos qui ratione voluptatem sequi nesciunt.</p>
  <a class="btn">Read More</a>
  <div class="photo" role="img" aria-label="Driver standing in front of a red truck" style="left:771px;top:39px;width:278px;height:278px;background:linear-gradient(160deg,#9aa7b3,#b52a2e 60%,#6b1a1c)"></div>
  <div class="photo" role="img" aria-label="Driver seated in a truck cab" style="left:663px;top:171px;width:266px;height:266px;background:linear-gradient(150deg,#6d7a84,#3a4148 60%,#22272b)"></div>
  <div class="photo" role="img" aria-label="Worker in a hi-vis vest beside a truck" style="left:905px;top:253px;width:176px;height:176px;background:linear-gradient(150deg,#a32a2c,#d36a2a 55%,#5a2020)"></div>
</section>

<section class="services">
  <svg class="abs" style="left:98px;top:1668px" width="430" height="430" viewBox="0 0 430 430"><path d="M30 250A185 185 0 0 1 380 110" fill="none" stroke="var(--red)" stroke-width="5"/><path d="M400 150A185 185 0 0 1 330 380" fill="none" stroke="var(--red)" stroke-width="5"/></svg>
  <div class="abs" role="img" aria-label="Truck hauling a tank trailer past bare trees" style="left:117px;top:1688px;width:384px;height:384px;border-radius:50%;background:linear-gradient(180deg,#c9ced3 0%,#a7adb2 45%,#5d6166 75%,#7c7f7a 100%)"></div>
  <h2>OUR SERVICES</h2>
  <p>Sed ut perspiciatis unde omnis iste natus error sit voluptatem accusantium doloremque laudantium, totam rem aperiam, eaque ipsa quae ab illo inventore veritatis et quasi architecto beatae vitae dicta sunt explicabo. Nemo enim ipsam voluptatem quia voluptas sit aspernatur aut odit aut fugit, sed quia consequuntur magni dolores eos qui ratione voluptatem sequi nesciunt.</p>
  <a class="btn">Read More</a>
</section>

<section class="jobs">
  <div class="abs" style="inset:0;background:rgba(0,0,0,.25)" role="img" aria-label="Dark red-toned photo of a truck driver and a rig"></div>
  <h2>EMPLOYMENT</h2>
  <div class="job" style="left:77px">
    <div class="pic" role="img" aria-label="Owner operators standing by their truck" style="background:linear-gradient(150deg,#c23036,#e9e4de 50%,#6a7480)"></div>
    <a class="apply">APPLY NOW</a>
    <h3>OWNER/OPERATORS</h3>
    <p>Sed ut perspiciatis unde omnis iste natus error sit voluptatem accusantium doloremque laudantium, totam rem aperiam, eaque ipsa quae ab illo</p>
  </div>
  <div class="job" style="left:436px">
    <div class="pic" role="img" aria-label="Company driver climbing into a red truck" style="background:linear-gradient(150deg,#3c3f44,#9b1d22 55%,#c7343a)"></div>
    <a class="apply">APPLY NOW</a>
    <h3>COMPANY DRIVERS</h3>
    <p>Sed ut perspiciatis unde omnis iste natus error sit voluptatem accusantium doloremque laudantium, totam rem aperiam, eaque ipsa quae ab illo</p>
  </div>
  <div class="job" style="left:796px">
    <div class="pic" role="img" aria-label="Mechanic working on a truck wheel" style="background:linear-gradient(150deg,#4a4f55,#7c8288 50%,#2e3135)"></div>
    <a class="apply">APPLY NOW</a>
    <h3>MECHANIC</h3>
    <p>Sed ut perspiciatis unde omnis iste natus error sit voluptatem accusantium doloremque laudantium, totam rem aperiam, eaque ipsa quae ab illo</p>
  </div>
</section>

<section class="map" role="img" aria-label="Street map of the area around the depot">
  <svg class="abs" style="left:376px;top:80px" width="24" height="34" viewBox="0 0 12 16"><path fill="var(--red)" d="M6 0a6 6 0 0 0-6 6c0 4.5 6 10 6 10s6-5.5 6-10a6 6 0 0 0-6-6zm0 8.5A2.5 2.5 0 1 1 6 3.5a2.5 2.5 0 0 1 0 5z"/></svg>
  <div class="mapcard">48 Harlow Creek Road, Kelmscott,<br>WA 6111<br>08 9400 1187<br>office@ridgelinehaul.com.au<br>Mon. - Sun: 09:00 - 19:00</div>
</section>

<footer class="footer">
  <div class="brand">RIDGELINE HAUL<br>CARRIERS</div>
  <h4 style="left:402px">Contact Us</h4>
  <div class="finfo" style="top:90px"><svg width="14" height="18" viewBox="0 0 12 16"><path d="M6 0a6 6 0 0 0-6 6c0 4.5 6 10 6 10s6-5.5 6-10a6 6 0 0 0-6-6zm0 8.5A2.5 2.5 0 1 1 6 3.5a2.5 2.5 0 0 1 0 5z"/></svg><span>48 Harlow Creek Road,<br>Kelmscott WA 6111</span></div>
  <div class="finfo" style="top:154px"><svg width="16" height="16" viewBox="0 0 16 16"><path d="M3.6 0 6 3.6 4.3 5.6a10 10 0 0 0 6.1 6.1l2-1.7L16 12.4 13.7 16C6 15.4.6 10 0 2.3z"/></svg><span>555 014 2290</span></div>
  <div class="finfo" style="top:202px"><svg width="16" height="12" viewBox="0 0 16 12"><path d="M0 0h16v12H0z"/></svg><span>info@ridgelinehaul.com</span></div>
  <h4 style="left:685px">Links</h4>
  <div class="flinks">Home<br>About<br>Services<br>Jobs<br>Contact</div>
  <h4 style="left:840px">Newsletter</h4>
  <div class="fnews">But I must explain to you how all this mistaken idea of enouncing pleasure and praising.</div>
  <div class="finput">Enter your email address</div>
  <div class="fgo"><svg width="16" height="12" viewBox="0 0 16 12"><path d="M0 6h13M9 1l5 5-5 5" fill="none" stroke="#fff" stroke-width="2"/></svg></div>
</footer>

<div class="copy">© 2019 Copyrights | All Rights Reserved</div>

</body>
</html>
```